Beautiful design for wordpress

I need a beautiful, colourful and feminine website. My business is called 'The Velvet Lantern', and I sell crystals, books, CD's, pendulums and other metaphysical items. I also provide Reiki (energy healing).
I want this design to be eye catching and inspire happiness and joy in those who see it. And I would love to see the use of the logo and its colours :)
Please add these on the web design: Home, About, Online store, Blog

Industry/Entity Type

Business

Requirements
Must have
• Colourful and playful, must use the logo somewhere, have the words on a menu saying 'Home, Blog, Online store and about' (or similar to those)And the design must stand out!
Should not have
• grey, brown and other boring colours.

```html
<!DOCTYPE html>
<html lang="en">
<head>
<meta charset="utf-8">
<title>The Velvet Lantern</title>
<link href="https://fonts.googleapis.com/css2?family=Oswald:wght@400&family=Open+Sans:wght@400;600&family=Roboto:wght@400&family=Great+Vibes&display=swap" rel="stylesheet">
<style>
:root{
  --pink:#f87a7d;
  --pink-dark:#f0656a;
  --orange:#fbab48;
  --green:#9ac44a;
  --magenta:#f154c3;
  --coral:#f87a7d;
  --amber:#fda33f;
  --text:#555;
  --dark:#222;
  --card:#ececec;
  --footer:#1e1e1e;
  --red:#e8483d;
  --lime:#8cc43c;
}
*{box-sizing:border-box;margin:0;padding:0}
html,body{width:845px;height:1200px;overflow:hidden;background:#fff;font-family:"Open Sans",Arial,sans-serif;color:var(--text)}
.page{position:relative;width:845px;height:1200px;border-top:3px solid var(--pink)}
.abs{position:absolute}
h2,h3{font-weight:400}
.brand{left:141px;top:14px;width:120px}
.brand-name{display:flex;align-items:center;gap:6px;font-weight:600;font-size:15px;line-height:1.1;color:var(--pink-dark)}
.brand-dot{width:12px;height:12px;border-radius:50%;background:var(--magenta);flex:none}
.brand-tag{font-size:5px;letter-spacing:1px;color:#444;margin:4px 0 0 18px}
.search{left:497px;top:41px;display:flex;align-items:center}
.search-field{width:108px;height:16px;border:1px solid #ccc;font-size:6px;color:#999;padding:4px 4px}
.search-btn{width:16px;height:16px;background:#333;position:relative}
.search-btn::before{content:"";position:absolute;left:4px;top:4px;width:6px;height:6px;border:1.5px solid #fff;border-radius:50%}
.search-btn::after{content:"";position:absolute;left:10px;top:10px;width:3px;height:1.5px;background:#fff;transform:rotate(45deg)}
.header-social{display:flex;gap:4px;margin-left:5px;font-size:6px;color:#666}
.contact{left:556px;top:63px;font-size:6.5px;color:#888;display:flex;gap:14px}
.nav{left:141px;top:98px;width:563px;height:35px;background:var(--pink);display:flex;align-items:center;font-family:"Oswald",sans-serif;font-size:8.5px;color:#fff}
.nav a{color:#fff;text-decoration:none}
.nav .home{background:var(--orange);width:69px;height:35px;display:flex;align-items:center;justify-content:center}
.nav-links{display:flex}
.nav-links a{margin-left:74px}
.nav-links a:first-child{margin-left:46px}
.nav-social{margin-left:auto;margin-right:9px;display:flex;gap:7px;font-family:"Open Sans",sans-serif;font-size:7px}
.hero{left:141px;top:141px;width:563px;height:301px;background:radial-gradient(ellipse at 60% 55%,#9aa8c8 0%,#4d5d86 30%,#1d2440 62%,#0c0f1c 100%)}
.hero-kicker{left:91px;top:85px;font-family:"Roboto",sans-serif;font-size:11px;color:#f3b21f}
.hero-title{left:92px;top:98px;font-family:"Great Vibes",cursive;font-size:56px;color:#f28c12}
.hero-btn{left:97px;top:192px;width:104px;height:26px;border-radius:13px;background:#f2f2f2;font-family:"Roboto",sans-serif;font-size:13px;color:#666;display:flex;align-items:center;justify-content:center;gap:5px}
.hero-btn i{width:9px;height:9px;border:1px solid #888;border-radius:50%}
.hero-arrow{top:127px}
.hero-dots{left:231px;top:280px;width:98px;height:21px;background:var(--pink);display:flex;justify-content:center;align-items:center;gap:5px}
.hero-dots span{width:6px;height:6px;border-radius:50%;background:#fff;opacity:.8}
.section-title{left:0;width:845px;text-align:center;font-family:"Oswald",sans-serif;font-size:18px;color:var(--pink)}
.divider{left:339px;width:168px;height:1px;background:#ddd}
.divider-mark{left:408px;width:30px;height:9px;background:#c4c4c4}
.intro{left:141px;top:498px;width:563px;text-align:center;font-size:6.4px;line-height:13.5px;color:#555}
.product{width:130px;height:154px;top:624px;box-shadow:0 0 2px rgba(0,0,0,.25)}
.product-img{height:125px}
.product-label{height:29px;display:flex;align-items:center;justify-content:space-between;padding:0 8px;color:#fff;font-size:8.5px}
.product-label i{width:12px;height:12px;border-radius:50%;background:#fff;position:relative}
.product-label i::before,.product-label i::after{content:"";position:absolute;left:3px;top:5.3px;width:6px;height:1.5px;background:currentColor}
.product-label i::after{transform:rotate(90deg)}
.specials-head{left:141px;top:798px;font-family:"Roboto",sans-serif;font-size:13.5px;color:var(--pink)}
.specials-line{left:198px;top:808px;width:486px;height:1px;background:#ddd}
.special{width:180px;height:78px;background:var(--card);border:1px solid #ddd;display:flex}
.special-img{width:90px;height:76px;flex:none}
.special-info{padding:8px 0 0 6px;font-size:6.6px;line-height:11px;color:#222}
.special-info .by{color:var(--lime);font-size:5.4px}
.special-info .price,.special-info .add{color:var(--red)}
.newsletter{left:139px;top:1038px;width:563px;height:39px;border:1px solid #e4e4e4;border-radius:3px;display:flex;align-items:center;padding-left:10px}
.newsletter h3{font-size:13px;color:#333}
.newsletter-field{width:166px;height:18px;border:1px solid #ddd;margin-left:10px}
.newsletter-btn{margin-left:4px;background:var(--red);color:#fff;font-size:7px;font-weight:600;padding:4px 7px;border-radius:2px}
.follow{margin-left:20px;font-size:8.5px;color:#444}
.follow-links{display:flex;gap:12px;margin-left:14px;font-size:8px;color:var(--red)}
.footer{left:0;top:1112px;width:845px;height:88px;background:var(--footer);border-top:3px solid var(--pink)}
.footer-links{left:140px;top:24px;font-size:6.4px;color:#fff}
.footer-links b{font-weight:600}
.copy{left:140px;top:41px;font-size:6.4px;color:#fff}
.pay{width:28px;height:16px;border-radius:2px}
.foot-social{left:620px;top:34px;display:flex;gap:9px;font-size:7px;color:#ddd}
</style>
</head>
<body>
<div class="page">
  <header>
    <div class="abs brand">
      <div class="brand-name"><span class="brand-dot"></span>The Velvet Lantern</div>
      <div class="brand-tag">CRYSTALS &amp; GIFTS</div>
    </div>
    <div class="abs search">
      <div class="search-field">Search ...</div>
      <div class="search-btn"></div>
      <div class="header-social"><span>Glim</span><span>Chirp</span><span>Pinna</span><span>Linko</span></div>
    </div>
    <div class="abs contact"><span>&#9742; (555) 987-2210</span><span>&#9993; hello@velvetlantern.shop</span></div>
    <nav class="abs nav">
      <a class="home" href="#">Home</a>
      <div class="nav-links"><a href="#">About</a><a href="#">Online store</a><a href="#">Blog</a><a href="#">Contact us</a></div>
      <div class="nav-social"><span>Glim</span><span>Chirp</span></div>
    </nav>
  </header>

  <section class="abs hero" role="img" aria-label="Cluster of glowing blue and violet quartz crystals on a dark background">
    <div class="abs hero-kicker">Always fresh &amp; amazing</div>
    <div class="abs hero-title">Gifts</div>
    <div class="abs hero-btn"><i></i>Enter Shop</div>
    <svg class="abs hero-arrow" style="left:22px" width="16" height="28" viewBox="0 0 16 28"><path d="M13 2 3 14l10 12" fill="none" stroke="#f87a7d" stroke-width="3"/></svg>
    <svg class="abs hero-arrow" style="left:525px" width="16" height="28" viewBox="0 0 16 28"><path d="M3 2l10 12L3 26" fill="none" stroke="#f87a7d" stroke-width="3"/></svg>
    <div class="abs hero-dots"><span></span><span></span><span></span><span></span><span></span></div>
  </section>

  <h2 class="abs section-title" style="top:452px">Welcome To Velvet Lantern</h2>
  <div class="abs divider" style="top:488px"></div>
  <div class="abs divider-mark" style="top:484px" role="img" aria-label="Small grey ornament"></div>
  <p class="abs intro">Lorem ipsum dolor sit amet, consectetuer adipiscing elit, sed diam nonummy nibh euismod tincidunt ut laoreet dolore magna aliquam erat volutpat. Ut wisi enim ad minim veniam, quis nostrud exerci tation ullamcorper suscipit lobortis nisl ut aliquip ex ea commodo consequat.Lorem ipsum dolor sit amet, consectetuer adipiscing elit, sed diam nonummy nibh euismod tincidunt ut laoreet dolore magna aliquam erat volutpat. Ut wisi enim ad minim veniam, quis nostrud exerci tation ullamcorper suscipit lobortis nisl ut aliquip ex ea commodLorem ipsum dolor sit amet, consectetuer adipiscing elit, sed diam nonummy nibh euismod tincidunt ut laoreet dolore magna aliquam</p>

  <h2 class="abs section-title" style="top:566px">Products</h2>
  <div class="abs divider" style="top:599px"></div>
  <div class="abs divider-mark" style="top:595px" role="img" aria-label="Small grey ornament"></div>

  <div class="abs product" style="left:141px">
    <div class="product-img" role="img" aria-label="Hand wearing crystal rings and bracelet" style="background:linear-gradient(160deg,#8a6a52,#d2a88d 50%,#5a4030)"></div>
    <div class="product-label" style="background:var(--green);color:var(--green)"><span style="color:#fff">Cristal</span><i></i></div>
  </div>
  <div class="abs product" style="left:284px">
    <div class="product-img" role="img" aria-label="Open book in front of a bookshelf" style="background:linear-gradient(180deg,#5a3a20,#b88a55 55%,#e9d4ad)"></div>
    <div class="product-label" style="background:var(--magenta);color:var(--magenta)"><span style="color:#fff">Books</span><i></i></div>
  </div>
  <div class="abs product" style="left:428px">
    <div class="product-img" role="img" aria-label="Three crystal pendulums hanging on chains" style="background:linear-gradient(90deg,#0b0b0b,#2a3a2a 30%,#111 50%,#3a2a40 80%,#0b0b0b)"></div>
    <div class="product-label" style="background:var(--coral);color:var(--coral)"><span style="color:#fff">Pendulums</span><i></i></div>
  </div>
  <div class="abs product" style="left:571px">
    <div class="product-img" role="img" aria-label="Mystical figure holding a glowing moon in misty darkness" style="background:radial-gradient(ellipse at 55% 70%,#e6e6e6,#7a7a7a 40%,#1c1c1c 80%)"></div>
    <div class="product-label" style="background:var(--amber);color:var(--amber)"><span style="color:#fff">Metaphysical</span><i></i></div>
  </div>

  <h2 class="abs specials-head">Specials</h2>
  <div class="abs specials-line"></div>
  <svg class="abs" style="left:685px;top:803px" width="20" height="10" viewBox="0 0 20 10"><path d="M7 1 3 5l4 4" fill="none" stroke="#111" stroke-width="2"/><path d="M13 1l4 4-4 4" fill="none" stroke="#f87a7d" stroke-width="2"/></svg>

  <div class="abs special" style="left:141px;top:832px">
    <div class="special-img" role="img" aria-label="Stack of old books" style="background:linear-gradient(90deg,#0d0905,#8a6a3a 60%,#d9b878)"></div>
    <div class="special-info">Óculos de Sol Aurora<br>Lume (Novo)<br><span class="by">Produto de Usuário</span><br><span class="price">R$ 500,00</span><br><span class="add">Add Cart</span></div>
  </div>
  <div class="abs special" style="left:330px;top:832px">
    <div class="special-img" role="img" aria-label="Sparkling cut diamond" style="background:radial-gradient(ellipse at 50% 55%,#d8ecff,#4a7ab8 40%,#0a1a33 85%)"></div>
    <div class="special-info">Óculos de Sol Aurora<br>Lume (Novo)<br><span class="by">Produto de Usuário</span><br><span class="price">R$ 500,00</span><br><span class="add">Add Cart</span></div>
  </div>
  <div class="abs special" style="left:523px;top:832px">
    <div class="special-img" role="img" aria-label="Clear crystal pendant" style="background:radial-gradient(ellipse at 50% 60%,#c7c0b4,#4a3a2a 50%,#1a120a)"></div>
    <div class="special-info">Óculos de Sol Aurora<br>Lume (Novo)<br><span class="by">Produto de Usuário</span><br><span class="price">R$ 500,00</span><br><span class="add">Add Cart</span></div>
  </div>
  <div class="abs special" style="left:141px;top:930px">
    <div class="special-img" role="img" aria-label="Glowing violet crystal ball" style="background:radial-gradient(circle at 50% 55%,#f5dcff,#b47ae0 25%,#3a1a5a 55%,#0d0515)"></div>
    <div class="special-info">Óculos de Sol Aurora<br>Lume (Novo)<br><span class="by">Produto de Usuário</span><br><span class="price">R$ 500,00</span><br><span class="add">Add Cart</span></div>
  </div>
  <div class="abs special" style="left:330px;top:930px">
    <div class="special-img" role="img" aria-label="Rainbow reflections on music CDs" style="background:linear-gradient(135deg,#3a7af0,#e04ad0 30%,#f7d23a 55%,#4ac96a 75%,#2a3ab0)"></div>
    <div class="special-info">Óculos de Sol Aurora<br>Lume (Novo)<br><span class="by">Produto de Usuário</span><br><span class="price">R$ 500,00</span><br><span class="add">Add Cart</span></div>
  </div>
  <div class="abs special" style="left:523px;top:930px">
    <div class="special-img" role="img" aria-label="Relaxing Reiki energy healing session" style="background:linear-gradient(160deg,#e8c4a8,#c98a64 50%,#7a4a30)"></div>
    <div class="special-info">Óculos de Sol Aurora<br>Lume (Novo)<br><span class="by">Produto de Usuário</span><br><span class="price">R$ 500,00</span><br><span class="add">Add Cart</span></div>
  </div>

  <section class="abs newsletter">
    <h3>Sign Up For Newsletter:</h3>
    <div class="newsletter-field"></div>
    <div class="newsletter-btn">Subscribe</div>
    <span class="follow">Follow Me</span>
    <div class="follow-links"><span>Glim</span><span>Chirp</span><span>Feed</span></div>
  </section>

  <footer class="abs footer">
    <div class="abs footer-links">Home &nbsp;|&nbsp; About Us &nbsp;|&nbsp; Services &nbsp;|&nbsp; <b>News/Blog</b> &nbsp;|&nbsp; <b>Contact Us</b></div>
    <div class="abs copy">Copyright Velvet Lantern.&nbsp; All rights reserved.</div>
    <div class="abs pay" style="left:403px;top:15px;background:#f2f2f2"></div>
    <div class="abs pay" style="left:436px;top:15px;background:#2f7fd0"></div>
    <div class="abs pay" style="left:403px;top:34px;background:#e7a23a"></div>
    <div class="abs pay" style="left:436px;top:34px;background:#f2f2f2"></div>
    <div class="abs foot-social"><span>Glim</span><span>Chirp</span><span>Linko</span></div>
  </footer>
</div>
</body>
</html>
```